I need a 6 x 11 postcard created that adheres to the design templates of the Federated parcel bureau. It will be mailed to scholars to encourage them to attend and present papers at the Marrowgate Indie International Film Festival's "Frame, Signal, and Score Conference." It must be provocative and engaging like a film festival poster. One option would be to high light the glitz of Hollywood and the appeal of the beach/shoreline in Long Beach but that's just one idea and I would love for the designer to just come with something original. It should be artistically compelling in that it would cause someone to keep the postcard even if they didn't care about the event. It must stand out in the mail and on a bulletin board.

You DO NOT have to use logo that I included and you do not have to stick with color schemes that are on logo.

My notes are in red on the document that includes the text.

the front can be portrait or landscape but back must be landscape. Also, designs submitted should include front and back.

You do not have to use the logo I included. If you do use the logo you can change the colors to fit your design Ideas.

The postcard will be sent to scholars who study and write about film, television, music, and digital media. We are inviting them to participate in a conference by selling them hollywood and the beaches of southern california.

Festival

• The design must be bold and inventive. Either ultramodern or just artistically appealing. The words 'Frame, Signal, and Score Conference" and "Call for Papers, Films, and Exhibitors Now Open!" must be clear on the front. It should be bright and inviting or classically beautiful (e.g. black and white).

It must match the Federated Parcel Bureau design requirements for 6 x 11 postcards
• This has got to be taken seriously by some very creative and intelligent people who love art, film, etc.

```html
<!DOCTYPE html>
<html lang="en">
<head>
<meta charset="utf-8">
<title>Frame, Signal, and Score Conference — Postcard Front and Back</title>
<link rel="stylesheet" href="https://fonts.googleapis.com/css2?family=Inter:wght@200;300;400&display=swap">
<style>
  :root {
    --page-bg: #ececec;
    --paper: #f7f7f7;
    --paper-line: #8c8c8c;
    --ink-light: #f4f4f4;
    --ink-soft: #cfcfcf;
    --tone-deep: #1f1f1f;
    --tone-mid: #4a4a4a;
    --tone-pale: #d9d9d9;
    --rule: rgba(255, 255, 255, 0.85);
  }
  * { margin: 0; padding: 0; box-sizing: border-box; }
  html, body {
    width: 1200px;
    height: 781px;
    overflow: hidden;
    background: var(--page-bg);
    font-family: "Inter", "Helvetica Neue", Arial, sans-serif;
  }
  .postcard {
    position: absolute;
    overflow: hidden;
    box-shadow: 0 3px 12px rgba(0, 0, 0, 0.18);
  }

  /* Back side */
  .postcard--back {
    left: 60px;
    top: 30px;
    width: 600px;
    height: 327px;
    background: var(--paper);
  }
  .postcard__divider {
    position: absolute;
    left: 300px;
    top: 60px;
    width: 1px;
    height: 210px;
    background: var(--paper-line);
  }
  .postcard__stamp-box {
    position: absolute;
    right: 28px;
    top: 24px;
    width: 52px;
    height: 52px;
    border: 1.5px solid var(--paper-line);
  }
  .postcard__address-lines {
    position: absolute;
    left: 330px;
    top: 140px;
    width: 240px;
    list-style: none;
  }
  .postcard__address-lines li {
    height: 26px;
    border-bottom: 1px solid var(--paper-line);
  }

  /* Front side */
  .postcard--front {
    left: 450px;
    top: 372px;
    width: 700px;
    height: 382px;
  }
  .postcard__artwork {
    position: absolute;
    inset: 0;
    width: 100%;
    height: 100%;
  }
  .headline {
    position: absolute;
    left: 225px;
    top: 48px;
    display: flex;
    color: var(--ink-light);
    text-transform: uppercase;
  }
  .headline__column {
    width: 200px;
    padding: 0 14px;
  }
  .headline__column--event { text-align: right; }
  .headline__divider {
    width: 1px;
    height: 215px;
    background: var(--rule);
    flex: none;
  }
  .headline__title {
    font-weight: 200;
    font-size: 24px;
    line-height: 1.05;
    letter-spacing: 0;
  }
  .headline__detail {
    margin-top: 8px;
    font-weight: 300;
    font-size: 8px;
    line-height: 1.4;
    letter-spacing: 1.2px;
    color: var(--ink-soft);
  }
  .headline__deadline {
    margin-top: 62px;
  }
  .web-address {
    position: absolute;
    left: 18px;
    bottom: 12px;
    font-weight: 300;
    font-size: 7px;
    letter-spacing: 1.5px;
    color: var(--tone-mid);
    text-transform: uppercase;
  }
</style>
</head>
<body>
  <section class="postcard postcard--back" aria-label="Postcard back">
    <div class="postcard__stamp-box"></div>
    <div class="postcard__divider"></div>
    <ul class="postcard__address-lines">
      <li></li><li></li><li></li><li></li>
    </ul>
  </section>

  <main class="postcard postcard--front">
    <svg class="postcard__artwork" viewBox="0 0 700 382" preserveAspectRatio="none"
         role="img" aria-label="Black and white collage artwork: dark faceted cube pattern fading into pale smoky clouds and dotted spheres">
      <defs>
        <linearGradient id="artwork-tone" x1="1" y1="0" x2="0" y2="1">
          <stop offset="0" stop-color="#1f1f1f"/>
          <stop offset="0.45" stop-color="#4a4a4a"/>
          <stop offset="0.8" stop-color="#d9d9d9"/>
          <stop offset="1" stop-color="#8a8a8a"/>
        </linearGradient>
      </defs>
      <rect width="700" height="382" fill="url(#artwork-tone)"/>
    </svg>

    <section class="headline">
      <div class="headline__column headline__column--event">
        <h1 class="headline__title">Frame,<br>Signal,<br>and Score<br>Conference</h1>
        <p class="headline__detail">September 13–15<br>2015</p>
        <p class="headline__detail headline__deadline">Paper Deadline<br>April 1, 2015</p>
      </div>
      <div class="headline__divider"></div>
      <div class="headline__column headline__column--call">
        <h2 class="headline__title">Call for<br>Papers, Films,<br>and Exhibitors<br>Now Open!</h2>
        <p class="headline__detail">Marrowgate,<br>California</p>
      </div>
    </section>

    <p class="web-address">www.marrowgateindie.org</p>
  </main>
</body>
</html>
```